Powerpoint, Graphics for Sermon Series

I am starting a sermon series on the short letters if Scripture that are between Hebrews and Revelation. The sermon series will be called "Walking Unmarked Trails: Lasting Lessons from Quiet Hills."

Think about finding a packet of letters in an Attic. There is only the dialogue of the writer. We don't know exactly what the receivers were going through or even what their response to the letters were/are!

Target Market(s)

Local Church

Industry/Entity Type

Christian

Font styles to use
Serif
Sans Serif

Colors

Designer to choose colors to be used in the design.

Requirements
Must have
• Powerpoint Slide with Title -
• Background Slide -
• It would be great to have both JPG, PNG, and Photoshop/Indesign that can be used for powerpoint, both in 4x3 ration and wide... Need Title Slide with typography and background slide for text to go over the top of.
• Stick with the theme -- Walking Unmarked Trails
• I am including our church logo, but don't feel like you need to use it in anyway.
Nice to have
• Social Media Slides - Square Slide, Facebook Header
• Greyscale Version?

```html
<!DOCTYPE html>
<html lang="en">
<head>
<meta charset="utf-8">
<title>Walking Unmarked Trails – Content Slide</title>
<link rel="stylesheet" href="https://fonts.googleapis.com/css2?family=Lato:wght@400;700&family=Roboto+Slab:wght@700&display=swap">
<style>
  :root {
    --ink-brown: #5b3f2e;
    --body-text: #4a3a30;
    --subtitle-gold: #c98512;
    --band-orange: #f5a00a;
    --rule-orange: #eaa227;
    --paper: #fdfbf8;
  }
  html, body {
    margin: 0;
    padding: 0;
    width: 1200px;
    height: 900px;
    overflow: hidden;
    background: var(--paper);
  }
  .slide {
    position: relative;
    width: 1200px;
    height: 900px;
    overflow: hidden;
    font-family: "Lato", Arial, sans-serif;
  }
  .slide-backdrop {
    position: absolute;
    inset: 0;
    width: 1200px;
    height: 900px;
  }
  .slide-title {
    position: absolute;
    left: 48px;
    top: 26px;
    margin: 0;
    font-family: "Roboto Slab", "Rockwell", Georgia, serif;
    font-weight: 700;
    font-size: 54px;
    line-height: 1.15;
    color: var(--ink-brown);
    white-space: nowrap;
  }
  .title-rule {
    position: absolute;
    left: 0;
    top: 97px;
    width: 790px;
    height: 3px;
    background: var(--rule-orange);
  }
  .text-column {
    position: absolute;
    top: 212px;
    width: 408px;
  }
  .text-column--left { left: 36px; }
  .text-column--right { left: 518px; }
  .column-heading {
    margin: 0 0 4px;
    font-weight: 700;
    font-size: 31px;
    line-height: 1.3;
    color: var(--subtitle-gold);
  }
  .column-body {
    margin: 0;
    font-size: 21.5px;
    line-height: 37.5px;
    color: var(--body-text);
    text-align: justify;
    text-align-last: left;
    hyphens: manual;
  }
  .church-name {
    position: absolute;
    left: 20px;
    top: 822px;
    display: flex;
    align-items: center;
    gap: 10px;
    font-weight: 700;
    font-size: 24px;
    color: var(--ink-brown);
  }
  .church-mark {
    width: 18px;
    height: 18px;
    background: var(--ink-brown);
  }
</style>
</head>
<body>
<main class="slide">
  <svg class="slide-backdrop" viewBox="0 0 800 600" preserveAspectRatio="none">
    <defs>
      <linearGradient id="hazeFill" x1="0" y1="0" x2="0" y2="1">
        <stop offset="0" stop-color="#fbf7f3"/>
        <stop offset="0.55" stop-color="#f6efe9"/>
        <stop offset="1" stop-color="#efe5dc"/>
      </linearGradient>
      <linearGradient id="photoFill" x1="0" y1="0" x2="0.3" y2="1">
        <stop offset="0" stop-color="#efc489"/>
        <stop offset="0.45" stop-color="#e09a3c"/>
        <stop offset="1" stop-color="#b35f12"/>
      </linearGradient>
    </defs>
    <rect x="0" y="0" width="800" height="600" fill="url(#hazeFill)" role="img" aria-label="Faint hazy photograph of wooden crosses on a quiet hillside trail at sunrise"/>
    <path d="M565,0 Q810,300 555,600 L800,600 L800,0 Z" fill="var(--band-orange)"/>
    <path d="M612,0 Q796,300 575,600 L800,600 L800,0 Z" fill="#ffffff"/>
    <path d="M625,0 Q792,300 600,600 L800,600 L800,0 Z" fill="url(#photoFill)" role="img" aria-label="Warm orange-toned photograph of an old Bible with a cross on its cover"/>
  </svg>

  <h1 class="slide-title">Walking Unmarked Trails</h1>
  <div class="title-rule"></div>

  <section class="text-column text-column--left">
    <h2 class="column-heading">Subtext title here</h2>
    <p class="column-body">Lorem Ipsum is simply dummy text of the printing and typesetting industry. Lorem Ipsum has been the industry's standard dummy text ever since the 1500s, when an unknown printer took a galley of type and scrambled it to make a type specimen book. It has survived not only five centu&shy;ries, but also the leap into electronic type&shy;setting, remaining essentially unchanged. It was popularised in the 1960s with the release of Letraset sheets containing Lorem Ipsum passages</p>
  </section>

  <section class="text-column text-column--right">
    <h2 class="column-heading">Subtext title here</h2>
    <p class="column-body">Lorem Ipsum is simply dummy text of the printing and typesetting industry. Lorem Ipsum has been the industry's standard dummy text ever since the 1500s, when an unknown printer took a galley of type and scrambled it to make a type specimen book. It has survived not only five centu&shy;ries, but also the leap into electronic type&shy;setting, remaining essentially unchanged. It was popularised in the 1960s with the release of Letraset sheets containing Lorem Ipsum passages</p>
  </section>

  <div class="church-name">
    <span class="church-mark"></span>
    <span>Cedar Ridge Church</span>
  </div>
</main>
</body>
</html>
```